8-page Visitor's Guide for Private Wildlife Ranch

We need a Visitor's Guide for Private Wildlife Ranch, where we can include important information for the clients during their stay as well as the many activities we and surrounding businesses have to offer... we are looking to keep it in line with our current web look and feel, as well as some of the included supporting documents, our rack card and our current tribe-fold brochure... I will be looking to update these as well in the near future with a supporting design... just looking for something a little more eye catching and up to date!

http:// mvqa.example.org/papers/mvqpubs/files/mvq_bk_q7000_0000bb.

the pdf above is something we really like!!!!

Im sure you are going to need more photos, but I was limited to what I could upload!

www. klranchhomestead. com is our website

Info about us: Are you looking for a truly unique Texas experience? K.L. Ranch Homestead is THE place! Whether you are looking for a day trip, a weekend adventure, or a place to host your next event or corporate retreat, join us at K.L. Ranch Homestead.

No matter what your needs and interests are, we offer a wide variety of activities to suit any group. K.L. Ranch Homestead has been the chosen destination for many weddings, events, and corporate retreats.

Target Market(s)

Tourism/Travel

Industry/Entity Type

Tourism

Font styles to use
Other font styles liked:
• Plantagenet Cherokee

Colors
fff3d1
ffffff

Requirements
Must have
• I have included a pdf with a lot of the text that I want.....
• Pages to include: Cover page, Important Information, Welcome Letter/Map, What to do while here, special events at the ranch, lodging options, things you might see during your stay, and a page for ads from local businesses
• colors
• 3e2a05 dark brown
• d2c0a4 light brown
• f3f2f1 light light brown
• font:
• Plantagenet Cherokee
Nice to have
• I want it to have an easy to read, rustic ranch look like with the feel of our website, but fun and exciting to make it inviting and welcoming
Should not have
• ehh pretty open to most anything but bright colors

```html
<!DOCTYPE html>
<html lang="en">
<head>
<meta charset="utf-8">
<title>K.L. Ranch Homestead — Visitor's Guide: Meals &amp; Lodging</title>
<link rel="stylesheet" href="https://fonts.googleapis.com/css2?family=Nunito+Sans:wght@800;900&family=Lora:wght@400;500&display=swap">
<style>
  :root {
    --cream: #fff3d1;
    --paper: #ffffff;
    --brown-dark: #3e2a05;
    --brown-light: #d2c0a4;
    --brown-faint: #f3f2f1;
    --mark-faint: #ebe8e4;
    --ink: #2a1f10;
  }
  * { margin: 0; padding: 0; box-sizing: border-box; }
  html, body { width: 1200px; height: 900px; overflow: hidden; }
  body { background: var(--cream); position: relative; font-family: "Lora", Georgia, serif; color: var(--ink); }

  .page {
    position: absolute; top: 42px; width: 506px; height: 788px;
    background: var(--paper); overflow: hidden;
    box-shadow: 6px 6px 6px rgba(120, 100, 60, 0.25);
  }
  .page--meals { left: 84px; }
  .page--lodging { left: 614px; }

  .page-title {
    position: absolute; top: 48px; font-family: "Nunito Sans", Arial, sans-serif;
    font-weight: 900; font-size: 46px; letter-spacing: -0.5px; color: var(--brown-dark); line-height: 1;
  }
  .page-title__kicker {
    position: absolute; left: 130px; top: -20px;
    font-size: 21px; font-weight: 800; letter-spacing: 0; white-space: nowrap;
  }
  .title-bar { position: absolute; top: 67px; height: 21px; background: var(--brown-light); }

  .faint-name {
    position: absolute; top: 538px; text-align: center; white-space: nowrap;
    font-family: "Lora", Georgia, serif; font-size: 28px; font-weight: 500;
    color: var(--mark-faint); line-height: 1.2;
  }
  .page--meals .faint-name { left: 0; width: 100%; }
  .page--lodging .faint-name { left: 130px; width: 376px; }

  .intro { position: absolute; left: 71px; top: 136px; font-size: 15px; }

  .meal-row { position: absolute; left: 0; width: 420px; height: 88px; }
  .meal-row__band { position: absolute; left: 0; top: 25px; width: 120px; height: 38px; background: var(--brown-light); }
  .meal-row__icon { position: absolute; left: 74px; top: 0; width: 88px; height: 88px; border-radius: 50%; background: var(--brown-light); }
  .meal-row__icon svg { width: 88px; height: 88px; display: block; }
  .meal-row__text { position: absolute; left: 186px; top: 34px; font-size: 14px; }

  .photo-round {
    position: absolute; left: 361px; top: 194px; width: 236px; height: 236px; border-radius: 50%;
    border: 5px solid var(--brown-faint);
    background: linear-gradient(180deg, #c9ccd0 0%, #9aa19d 30%, #6e6a5c 45%, #3fa9c2 62%, #2b8fa8 80%, #b9ae98 100%);
  }

  .extras { position: absolute; left: 71px; top: 482px; list-style: none; font-size: 14px; line-height: 18px; }
  .extras li::before { content: "• "; }

  .photo-bottom { position: absolute; left: 0; bottom: 0; width: 506px; height: 214px; }
  .photo-bottom svg { display: block; }

  .photo-tall {
    position: absolute; left: 0; top: 118px; width: 118px; height: 422px;
    border-radius: 0 10px 10px 0; border: 5px solid #dfe3ec; border-left: none;
    background: linear-gradient(180deg, #8fa9d6 0%, #a7b9d8 28%, #9c7a4c 45%, #5f7a3a 65%, #6f8a49 85%, #8b8a6a 100%);
  }

  .lodging-list { position: absolute; left: 138px; top: 135px; list-style: none; }
  .lodging-list li {
    width: 208px; height: 20px; margin-bottom: 17.6px; padding-left: 8px;
    background: var(--brown-light); border-radius: 0 10px 10px 0;
    font-size: 14px; line-height: 20px; color: var(--ink);
  }
  .lodging-list li::before { content: "• "; }
</style>
</head>
<body>

<section class="page page--meals">
  <div class="title-bar" style="left:0;width:49px"></div>
  <div class="title-bar" style="left:208px;width:298px"></div>
  <h1 class="page-title" style="left:66px">Meals</h1>

  <p class="faint-name">K.L. Ranch Homestead</p>

  <p class="intro">Typically served buffet style in our chuckwagon</p>

  <div class="meal-row" style="top:171px">
    <div class="meal-row__band"></div>
    <div class="meal-row__icon">
      <svg viewBox="0 0 88 88" aria-hidden="true" fill="var(--brown-dark)">
        <path d="M14 44c0-8 7-13 13-12-4 4-4 14 0 20-6 1-13-2-13-8z"/>
        <path d="M38 40h24v12c0 7-5 11-12 11s-12-4-12-11z"/>
        <path d="M62 43h3a5 5 0 0 1 0 10h-3v-3h3a2 2 0 0 0 0-4h-3z"/>
        <path d="M46 36c-3-4 3-6 0-11M52 36c-3-4 3-6 0-11" stroke="var(--brown-dark)" stroke-width="2" fill="none"/>
      </svg>
    </div>
    <p class="meal-row__text">Breakfast is served at 8:00 AM</p>
  </div>

  <div class="meal-row" style="top:269px">
    <div class="meal-row__band"></div>
    <div class="meal-row__icon">
      <svg viewBox="0 0 88 88" aria-hidden="true" fill="var(--brown-dark)" stroke="var(--brown-dark)" stroke-linecap="round">
        <path d="M30 34a14 14 0 0 1 28 0" fill="none" stroke-width="3"/>
        <path d="M44 12v7M28 18l4 6M60 18l-4 6M20 30l6 3M68 30l-6 3" stroke-width="3"/>
        <path d="M36 40v10M40 40v10M44 40v10M36 50h8M40 50v24" stroke-width="3"/>
        <path d="M52 40c5 2 5 14 0 16v18" stroke-width="3" fill="var(--brown-dark)"/>
      </svg>
    </div>
    <p class="meal-row__text">Lunch is served at Noon</p>
  </div>

  <div class="meal-row" style="top:367px">
    <div class="meal-row__band"></div>
    <div class="meal-row__icon">
      <svg viewBox="0 0 88 88" aria-hidden="true" fill="var(--brown-dark)" stroke="var(--brown-dark)" stroke-linecap="round">
        <circle cx="44" cy="44" r="13" fill="none" stroke-width="4"/>
        <circle cx="44" cy="44" r="6"/>
        <path d="M20 30v10M24 30v10M28 30v10M20 40h8M24 40v18" stroke-width="3"/>
        <path d="M64 30c5 2 5 14 0 16v12" stroke-width="3"/>
        <path d="M70 30v28" stroke-width="3"/>
      </svg>
    </div>
    <p class="meal-row__text">Dinner is served at 7:00 PM</p>
  </div>

  <div class="photo-round" role="img" aria-label="Photo of the poolside pavilion with a blue swimming pool under a grey sky"></div>

  <ul class="extras">
    <li>Open Bar from 6:00 p.m. - Midnight</li>
    <li>Snacks available for purchase in front office.</li>
  </ul>

  <div class="photo-bottom" role="img" aria-label="Photo of a guest greeting a giraffe among green trees">
    <svg width="506" height="214" viewBox="0 0 506 214">
      <defs>
        <linearGradient id="treesGrad" x1="0" y1="0" x2="1" y2="0">
          <stop offset="0" stop-color="#3e5a2c"/>
          <stop offset="0.5" stop-color="#4f6b36"/>
          <stop offset="0.8" stop-color="#8a6a46"/>
          <stop offset="1" stop-color="#c9d3dd"/>
        </linearGradient>
      </defs>
      <polygon points="0,4 256,46 506,4 506,0 256,38 0,0" fill="#8d8a85"/>
      <polygon points="0,10 256,50 506,10 506,214 0,214" fill="url(#treesGrad)"/>
    </svg>
  </div>
</section>

<section class="page page--lodging">
  <div class="title-bar" style="left:0;width:48px"></div>
  <div class="title-bar" style="left:262px;width:244px"></div>
  <h1 class="page-title" style="left:66px">Lodging<span class="page-title__kicker">options</span></h1>

  <p class="faint-name">K.L. Ranch Homestead</p>

  <div class="photo-tall" role="img" aria-label="Photo of a tall giraffe standing among green brush under a blue sky"></div>

  <ul class="lodging-list">
    <li>Old Town Rooms</li>
    <li>Suites</li>
    <li>Mesa House</li>
    <li>Cedar 4 House</li>
    <li>Cedar 3 House</li>
  </ul>

  <div class="photo-bottom" role="img" aria-label="Photo of a stone fire-pit terrace overlooking the hills at sunset">
    <svg width="506" height="214" viewBox="0 0 506 214">
      <defs>
        <linearGradient id="sunsetGrad" x1="0" y1="0" x2="0" y2="1">
          <stop offset="0" stop-color="#7f86a8"/>
          <stop offset="0.25" stop-color="#c79b8e"/>
          <stop offset="0.38" stop-color="#e8b586"/>
          <stop offset="0.45" stop-color="#2f3826"/>
          <stop offset="0.58" stop-color="#4a4c4a"/>
          <stop offset="1" stop-color="#6e6a66"/>
        </linearGradient>
      </defs>
      <polygon points="0,8 256,44 506,8 506,4 256,38 0,2" fill="#dde2ea"/>
      <polygon points="0,10 256,46 506,10 506,214 0,214" fill="url(#sunsetGrad)"/>
    </svg>
  </div>
</section>

</body>
</html>
```